Corvane Paintless Dent Removal

Our company works on vehicles removing dents using a highly skilled trade which the metal is massaged out with special tools without disturbing the original paint, hence paintless dent removal. Besides keeping the paint and metal original its also very environmentally friendly since no paint or toxic fillers are used. Also we we are one of the most experienced companies in the business with 25 years

Target Market(s)

Retail Automobile consumers, Auto Dealerships and Auto Body Shops

Industry/Entity Type

Auto Repair

Contact Information for Business Card

Dale Hollister
PO Box 518 Brookmere, NY 11962
631-555-0148
corvanepdr@mailbox-example.com
website corvanepdr.example
youtube corvane paintless dent removal
25 years of experience removing Dents, Dings and Hail Damage

Font styles to use
Serif
Sans Serif

Colors

Designer to choose colors to be used in the design.

Requirements
Must have
• I do like things that are simple but classy and somewhat bold, also I like my logo so that should be somewhat important

```html
<!DOCTYPE html>
<html lang="en">
<head>
<meta charset="utf-8">
<title>Corvane Paintless Dent Removal – Business Card</title>
<link href="https://fonts.googleapis.com/css2?family=Roboto:wght@400;700;900&display=swap" rel="stylesheet">
<style>
  :root {
    --page: #3a3a3c;
    --card: #232324;
    --blue: #0a4a8f;
    --green: #7cc623;
    --text: #e6e6e6;
    --muted: #c9c9c9;
  }
  * { margin: 0; padding: 0; box-sizing: border-box; }
  html, body { width: 799px; height: 1200px; overflow: hidden; }
  body {
    background: var(--page);
    font-family: "Roboto", Arial, sans-serif;
    color: var(--text);
    position: relative;
  }
  .card {
    position: absolute;
    left: 40px;
    width: 719px;
    height: 410px;
    background: var(--card);
    border-radius: 4px;
    box-shadow: 0 10px 30px rgba(0,0,0,.45);
    overflow: hidden;
  }
  .card--front { top: 120px; }
  .card--back { top: 670px; }

  .brand {
    position: absolute;
    text-align: center;
    color: var(--green);
    font-weight: 900;
    line-height: 1.05;
  }
  .card--front .brand {
    left: 0; right: 0; top: 138px;
    font-size: 58px;
  }
  .card--front .brand small { display: block; font-size: 28px; font-weight: 900; margin-top: 8px; }
  .brand-dot {
    display: inline-block; width: 20px; height: 20px; border-radius: 50%;
    background: var(--green); margin-right: 14px; vertical-align: 6px;
  }

  .card--back .brand {
    left: 300px; top: 32px; width: 360px;
    font-size: 40px;
  }
  .card--back .brand small { display: block; font-size: 19px; font-weight: 900; margin-top: 6px; }
  .card--back .brand-dot { width: 14px; height: 14px; margin-right: 10px; vertical-align: 4px; }

  .person { position: absolute; left: 42px; top: 150px; }
  .person-name { color: var(--green); font-size: 30px; font-weight: 700; }
  .person-role { font-size: 15px; color: var(--muted); margin-top: 4px; }
  .experience { position: absolute; left: 42px; top: 240px; font-size: 15px; line-height: 1.35; color: var(--text); }

  .contact { position: absolute; left: 400px; top: 200px; font-size: 16px; line-height: 1.45; list-style: none; }
  .contact li { display: flex; align-items: center; gap: 12px; }
  .contact li.address { display: block; margin-bottom: 6px; padding-left: 0; }
  .contact svg { width: 14px; height: 14px; fill: var(--green); flex: none; }

  .stripe-green {
    position: absolute; left: 0; bottom: 70px; width: 330px; height: 12px; background: var(--green);
  }
  .band-blue {
    position: absolute; right: 0; bottom: 0; width: 420px; height: 70px; background: var(--blue);
    clip-path: polygon(60px 0, 100% 0, 100% 100%, 0 100%);
    display: flex; align-items: center; padding-left: 100px; font-size: 17px; color: #fff;
  }
  .band-blue .marker { width: 14px; height: 14px; background: #fff; margin-right: 12px; }
</style>
</head>
<body>
  <section class="card card--front">
    <div class="brand"><span class="brand-dot"></span>Corvane<small>Paintless Dent Removal</small></div>
  </section>

  <section class="card card--back">
    <div class="brand"><span class="brand-dot"></span>Corvane<small>Paintless Dent Removal</small></div>

    <div class="person">
      <p class="person-name">Dale Hollister</p>
      <p class="person-role">Managing Director</p>
    </div>
    <p class="experience">25 years of experience removing<br>Dents, Dings and Hail Damage</p>

    <ul class="contact">
      <li class="address">PO Box 518 Brookmere,<br>NY 11962</li>
      <li><svg viewBox="0 0 24 24"><path d="M6.6 10.8a15 15 0 0 0 6.6 6.6l2.2-2.2a1 1 0 0 1 1-.25 11.4 11.4 0 0 0 3.6.57 1 1 0 0 1 1 1V20a1 1 0 0 1-1 1A17 17 0 0 1 3 4a1 1 0 0 1 1-1h3.5a1 1 0 0 1 1 1c0 1.25.2 2.45.57 3.57a1 1 0 0 1-.25 1z"/></svg>631-555-0148</li>
      <li><svg viewBox="0 0 24 24"><path d="M2 5h20v14H2z M2 5l10 8 10-8" stroke="#232324" stroke-width="1.6"/></svg>corvanepdr@mailbox-example.com</li>
      <li><svg viewBox="0 0 24 24"><circle cx="12" cy="12" r="10"/><path d="M2 12h20M12 2c3 3 3 17 0 20M12 2c-3 3-3 17 0 20" stroke="#232324" stroke-width="1.4" fill="none"/></svg>www.corvanepdr.example</li>
    </ul>

    <div class="stripe-green"></div>
    <div class="band-blue"><span class="marker"></span>videohub.example/DaleHollister</div>
  </section>
</body>
</html>
```